RW Framewell Inc Business cards

We need business cards using our existing logo but slightly modified. Right now the logo says RW Loadbearing Masonry. We want to keep the RW part of the design, but replace the Structural Concrete portion with "FRAMEWELL". Please see the attached file.
Ideally this would be a blank template so we can add Different Names, titles, and phone numbers later.
On the one side we want only the logo and on the other side the detail. I'm attaching an example for you to see.
Please reach out with any other questions. Our address and other details will be given out once we find a design we like.

Target Market(s)

Construction Industry

```html
<!DOCTYPE html>
<html lang="en">
<head>
<meta charset="utf-8">
<title>RW Framewell Inc — Business Cards</title>
<link href="https://fonts.googleapis.com/css2?family=Montserrat:wght@600&family=Roboto:wght@400;500&display=swap" rel="stylesheet">
<style>
  :root {
    --backdrop: #5b83bc;
    --brand-blue: #2d62a3;
    --card-white: #f7f7f5;
    --ink-grey: #5e5e5e;
    --rule-blue: #2d62a3;
  }
  * { margin: 0; padding: 0; box-sizing: border-box; }
  html, body { width: 1200px; height: 852px; overflow: hidden; }
  body {
    background: var(--backdrop);
    font-family: "Roboto", Arial, sans-serif;
    position: relative;
  }
  .card {
    position: absolute;
    top: 276px;
    width: 520px;
    height: 300px;
    border-radius: 22px;
    box-shadow: 0 6px 18px rgba(20, 40, 80, 0.28);
  }
  .card-back { left: 50px; background: var(--brand-blue); }
  .card-front { left: 630px; background: var(--card-white); }

  .wordmark {
    position: absolute;
    left: 0; right: 0;
    text-align: center;
    font-family: "Montserrat", Arial, sans-serif;
    font-weight: 600;
    line-height: 1;
  }
  .wordmark .initials { display: block; font-size: 78px; letter-spacing: 2px; }
  .wordmark .name { display: block; font-size: 24px; letter-spacing: 6px; margin-top: 6px; }
  .card-back .wordmark { top: 92px; color: #ffffff; }
  .card-front .wordmark { top: 38px; color: var(--brand-blue); }
  .card-front .wordmark .initials { font-size: 60px; }
  .card-front .wordmark .name { font-size: 19px; letter-spacing: 5px; }

  .person {
    position: absolute;
    left: 34px;
    top: 178px;
    width: 220px;
    text-align: right;
  }
  .person-name { color: var(--brand-blue); font-weight: 500; font-size: 19px; }
  .person-title { color: var(--ink-grey); font-size: 13px; margin-top: 2px; }
  .person-rule { border: 0; border-top: 1.5px solid var(--rule-blue); margin: 7px 0 7px; }
  .person-address { color: var(--ink-grey); font-size: 13px; line-height: 1.35; }

  .contact {
    position: absolute;
    left: 290px;
    top: 178px;
    list-style: none;
  }
  .contact li {
    display: flex;
    align-items: center;
    gap: 10px;
    color: var(--ink-grey);
    font-size: 13px;
    height: 23px;
  }
  .contact svg { width: 12px; height: 12px; fill: var(--brand-blue); flex: none; }
</style>
</head>
<body>
  <section class="card card-back" aria-label="Card back">
    <div class="wordmark">
      <span class="initials">RW</span>
      <span class="name">FRAMEWELL</span>
    </div>
  </section>

  <section class="card card-front" aria-label="Card front">
    <div class="wordmark">
      <span class="initials">RW</span>
      <span class="name">FRAMEWELL</span>
    </div>

    <div class="person">
      <p class="person-name">Dana RW Ellison</p>
      <p class="person-title">Managing Director</p>
      <hr class="person-rule">
      <p class="person-address">88 Sample Rd., Placetown,<br>Oregon, US 970012</p>
    </div>

    <ul class="contact">
      <li>
        <svg viewBox="0 0 12 12" aria-hidden="true"><path d="M2.5 1 L4.5 1 L5.3 3.4 L4 4.4 C4.6 5.8 6.2 7.4 7.6 8 L8.6 6.7 L11 7.5 L11 9.5 C11 10.4 10.3 11 9.5 11 C5 11 1 7 1 2.5 C1 1.7 1.6 1 2.5 1 Z"/></svg>
        555-010-2040
      </li>
      <li>
        <svg viewBox="0 0 12 12" aria-hidden="true"><path d="M1 2.5 H11 V9.5 H1 Z M1.6 3 L6 6.6 L10.4 3 Z" fill-rule="evenodd"/></svg>
        dana@framewell-mail.com
      </li>
      <li>
        <svg viewBox="0 0 12 12" aria-hidden="true"><circle cx="6" cy="6" r="5"/><path d="M1 6 H11 M6 1 C3.8 3.5 3.8 8.5 6 11 C8.2 8.5 8.2 3.5 6 1" stroke="#f7f7f5" stroke-width="0.8" fill="none"/></svg>
        www.framewell-site.com
      </li>
    </ul>
  </section>
</body>
</html>
```